Moxy Fen needs some awesome stationary

Do you have what it takes to get my brand? You either do or you don't, have a crack at a design and you my just win my business.

I don't want to waste your or my time, so put your creative genius on either a business card or envelope.

I however need a package of stationary that follows the same brand. I will message you to complete the remaining should I like your first submission.

Here is what I need, have a go!

Basically I need the following for my small business based in melbourne.
- Letterhead (printer ready and MS Word)
- Business Card
- Compliments Slip
- Envelope
- Proposal Cover Page (MS Word only)
- Presentation Folder
- Marbled Fox Cards
- Student Name Tent
- Index Cards
- Vell-Ka

I am establishing the brand and it must be modern, professional but also relaxed; that is not formal and not corporate. It represents a company are leaders, but small enough to care and operate like a bunch of friends. We are bringing people and conversations back to business, and turfing out all the bureaucracy and crazy and wasteful procedures. Its about "lets talk and figure it out together and find even better ways".

Target Market(s)

Mainly companies that build software products, but Agile practices are used in many other industries (even graphic design projects)

Industry/Entity Type

Information Technology

Font styles to use
Sans Serif

Colors
3176b5
aaaaaa

Requirements
Must have
• I like curves and circles and not boxes or rectangles.
• I want a colour rich design with my brand colours, but it must be balanced.
• I want more modern than traditional, but simple modern
Should not have
• Not corporate
• Please don't waste my time if your not going to think about it.
• Don't mess with my primary logo
• Don't change my colours
• Don't overlay logo on image

```html
<!DOCTYPE html>
<html lang="en">
<head>
<meta charset="utf-8">
<title>Moxy Fen – Presentation Folder</title>
<link href="https://fonts.googleapis.com/css2?family=Open+Sans:wght@400;600;700&display=swap" rel="stylesheet">
<style>
  :root {
    --stage: #8a8a8d;
    --brand-blue: #2d5ba1;
    --brand-grey: #96a0b0;
    --paper: #ffffff;
    --paper-tint: #eef2f7;
    --ink-light: #ffffff;
  }
  html, body {
    margin: 0;
    padding: 0;
    width: 1200px;
    height: 875px;
    overflow: hidden;
    background: var(--stage);
  }
  .folder-dieline {
    display: block;
    width: 1200px;
    height: 875px;
    font-family: "Open Sans", Arial, sans-serif;
  }
  .panel { fill: var(--brand-blue); }
  .cover-window { fill: url(#window-wash); }
  .cover-swoosh { fill: var(--brand-grey); }
  .brand-name { fill: var(--brand-blue); font-weight: 700; font-size: 44px; }
  .brand-dot { fill: var(--brand-blue); }
  .hotline { fill: var(--ink-light); font-weight: 600; font-size: 31px; }
  .cover-url { fill: var(--ink-light); font-size: 14px; letter-spacing: 1.6px; }
  .flap-url { fill: var(--ink-light); font-size: 10px; letter-spacing: 3.4px; }
  .contact-line { fill: var(--ink-light); font-size: 10.5px; }
  .contact-icon { fill: var(--ink-light); }
</style>
</head>
<body>
<svg class="folder-dieline" viewBox="0 0 1317 960" preserveAspectRatio="none" role="img" aria-label="Moxy Fen presentation folder, flat die-cut layout">
  <defs>
    <radialGradient id="window-wash" cx="0.45" cy="0.35" r="0.8">
      <stop offset="0" stop-color="var(--paper-tint)"/>
      <stop offset="0.6" stop-color="#f6f8fb"/>
      <stop offset="1" stop-color="var(--paper)"/>
    </radialGradient>
  </defs>

  <!-- top flap -->
  <path class="panel flap-top" d="M630,226 V135 C730,90 850,55 962,42 L992,80 C1010,65 1040,80 1055,105 C1068,130 1066,160 1040,160 L1080,218 V226 Z"/>

  <!-- side flap -->
  <path class="panel flap-side" d="M1082,226 L1238,282 L1160,640 C1150,680 1130,697 1105,697 H1082 Z"/>

  <!-- back panel -->
  <rect class="panel back-panel" x="146" y="226" width="464" height="636"/>

  <!-- front cover -->
  <rect class="panel front-panel" x="610" y="226" width="472" height="636"/>

  <!-- cover window -->
  <path class="cover-window" role="img" aria-label="Soft light wash of curved shapes" d="M610,226 H1082 V590 C1020,660 930,702 846,702 C760,702 670,660 610,590 Z"/>

  <!-- grey swoosh -->
  <path class="cover-swoosh" d="M1082,370 C1060,470 1010,560 930,630 C880,670 830,686 790,690 C860,694 960,672 1030,630 C1052,616 1068,602 1082,588 Z"/>

  <!-- brand name -->
  <circle class="brand-dot" cx="842" cy="420" r="26"/>
  <text class="brand-name" x="842" y="520" text-anchor="middle">Moxy Fen</text>

  <!-- cover contact -->
  <text class="hotline" x="844" y="790" text-anchor="middle">13 000 MOXY</text>
  <text class="cover-url" x="846" y="811" text-anchor="middle">www.moxy-fen.com.au</text>

  <!-- flap url -->
  <text class="flap-url" transform="translate(1142,510) rotate(-90)">www.moxy-fen.com.au</text>

  <!-- back contact block -->
  <g class="contact-block">
    <text class="contact-line" x="176" y="748">PO Box 4187</text>
    <text class="contact-line" x="176" y="762">Kelverton North</text>
    <text class="contact-line" x="176" y="775">VIC 3190, Australia</text>
    <text class="contact-line" x="177" y="791">Moxy Fen Pty Ltd</text>
    <text class="contact-line" x="177" y="805">ABN 48 912 305 774</text>
    <path class="contact-icon" d="M178,814 l3,-1 l2,3 l-1.5,1.5 c1,2 2,3 4,4 l1.5,-1.5 l3,2 l-1,3 c-6,0 -11,-5 -11,-11 z"/>
    <text class="contact-line" x="193" y="822">13 000 MOXY</text>
    <circle class="contact-icon" cx="182" cy="833" r="5"/>
    <text class="contact-line" x="193" y="836">www.moxy-fen.com.au</text>
  </g>
</svg>
</body>
</html>
```